Web Design for a Biotech Consulting Firm

We need a web site design for a new business based in Philadelphia called Verantel Dx. This is a consulting firm that will serve medical diagnostics industry, which is part of the life science/healthcare industry focusing on developing and marketing products that help in early detection, monitoring or management of diseases. Our consulting firm will help medical diagnostic companies to overcome key challenges in designing, evaluating and marketing new products.Our company name is Verantel Dx. Verantel is Latin word for "something" Dx represents diagnostics. The idea behind the name is that we help companies to transform the original, early product ideas ("nothing") into "something"; which is a product with full clinical utility that will help to improve health and well-being.The web site should use the visual feel of the logo (attached), be modern, simple and clean looking and represent creativity, innovation, scientific thinking and progress.
Updates

Wix Design is acceptable

Industry/Entity Type

Biotechnology

Coding

Coded - Design and coding required

Number of Pages Required

1 page

Font styles to use
Sans Serif

Requirements
Must have
• simple, clean look couple of pages
Should not have
• a lot of pages

```html
<!DOCTYPE html>
<html lang="en">
<head>
<meta charset="utf-8">
<title>Verantel Dx – Medical Diagnostics Consulting</title>
<link rel="stylesheet" href="https://fonts.googleapis.com/css2?family=Poppins:wght@400;500;600&family=Lato:wght@400;700&display=swap">
<style>
:root{
  --blue:#1f80ea;
  --blue-dark:#176ccc;
  --ink:#111418;
  --text:#3a3f45;
  --muted:#8b9097;
  --white:#ffffff;
  --black:#050607;
}
*{margin:0;padding:0;box-sizing:border-box}
html,body{width:1200px;height:4167px;overflow:hidden;background:var(--white)}
body{position:relative;font-family:'Lato',sans-serif;color:var(--text)}
.abs{position:absolute}
h1,h2,h3,h4{font-family:'Poppins',sans-serif;font-weight:500;color:var(--ink)}
.accent{color:var(--blue)}
.btn{position:absolute;display:flex;align-items:center;justify-content:center;background:var(--blue);color:var(--white);font-family:'Lato',sans-serif;font-size:16px;border-radius:3px;box-shadow:0 4px 0 var(--blue-dark);text-decoration:none}
.photo{position:absolute}

/* header */
.brand{left:78px;top:46px;display:flex;align-items:center;gap:10px;font-family:'Poppins',sans-serif;font-weight:500;font-size:20px;color:var(--ink);white-space:nowrap}
.brand-mark{width:14px;height:14px;background:var(--blue)}
.nav a{position:absolute;top:51px;font-size:16px;color:#999fa6;text-decoration:none}
.nav a.active{color:var(--blue);font-weight:700}
.phone-btn{left:925px;top:36px;width:197px;height:51px;font-size:19px;font-weight:700;gap:12px}

/* hero */
.hero-title{left:78px;top:215px;font-size:82px;font-weight:600;letter-spacing:-1px;white-space:nowrap}
.hero-sub{left:78px;top:315px;font-size:44px;line-height:51px;color:var(--text)}

.section-title{font-size:44px;white-space:nowrap}
.para{font-size:14px;line-height:26px;color:var(--muted)}

/* services */
.card{position:absolute;top:1332px;width:332px;height:416px;background:var(--white)}
.card .photo{left:11px;top:10px;width:310px;height:209px}
.card h3{position:absolute;left:12px;top:236px;font-size:22px;color:var(--blue)}
.card p{position:absolute;left:12px;top:278px;width:310px;font-size:13.5px;line-height:26px;color:var(--muted)}
.card .more{position:absolute;left:12px;top:367px;font-size:15px;color:var(--ink)}

/* feedback */
.quote{position:absolute;top:2000px;width:271px;height:269px;background:var(--white);box-shadow:0 2px 10px rgba(0,0,0,.13)}
.quote svg{position:absolute;left:21px;top:40px}
.quote p{position:absolute;left:22px;top:88px;width:232px;font-size:13.5px;line-height:26px;color:var(--muted)}
.quote .who{position:absolute;left:22px;top:210px;font-family:'Poppins',sans-serif;font-size:15px;color:var(--ink)}
.arrow{position:absolute;top:2110px;width:36px;height:50px;display:flex;align-items:center;justify-content:center}

/* contact */
.field{position:absolute;background:var(--white);border-radius:2px;font-size:13.5px;color:#6f757c;padding:18px 12px}

/* news */
.meta{position:absolute;top:3328px;display:flex;gap:40px;font-size:14px;color:var(--muted);align-items:center}
.meta span{display:flex;align-items:center;gap:8px}
.news-title{position:absolute;top:3370px;width:500px;font-size:18.5px;line-height:28px;color:var(--ink)}
.news-para{position:absolute;top:3434px;width:500px;font-size:13.5px;line-height:26px;color:var(--muted)}

/* footer */
.foot-h{position:absolute;top:3785px;font-size:19px;color:var(--white)}
.foot-list{position:absolute;top:3830px;list-style:none;font-size:14px;color:var(--white);line-height:31px}
.foot-list li::before{content:"- ";}
.contact-row{position:absolute;left:616px;display:flex;gap:16px;font-size:14px;color:var(--white);line-height:26px}
.social{position:absolute;top:3832px;width:47px;height:47px;border-radius:50%;background:var(--white)}
.foot-brand{left:0;top:4024px;width:1200px;display:flex;justify-content:center;align-items:center;gap:8px;font-family:'Poppins',sans-serif;font-size:13px;color:var(--white)}
.foot-brand i{width:9px;height:9px;background:var(--white)}
.copyright{position:absolute;top:4100px;left:0;width:1200px;text-align:center;font-size:14px;color:var(--white)}
</style>
</head>
<body>

<header>
  <div class="abs brand"><span class="brand-mark"></span>Verantel Dx</div>
  <nav class="nav">
    <a class="active" style="left:370px">Home</a>
    <a style="left:464px">About</a>
    <a style="left:558px">Services</a>
    <a style="left:668px">News</a>
    <a style="left:755px">Contact</a>
  </nav>
  <svg class="abs" style="left:858px;top:52px" width="22" height="22" viewBox="0 0 22 22" fill="none" stroke="#222" stroke-width="2"><circle cx="9" cy="9" r="7"/><line x1="14" y1="14" x2="20" y2="20"/></svg>
  <a class="btn phone-btn">
    <svg width="20" height="20" viewBox="0 0 24 24" fill="#fff"><path d="M6.6 10.8a15.1 15.1 0 0 0 6.6 6.6l2.2-2.2c.3-.3.7-.4 1-.2 1.1.4 2.3.6 3.6.6.6 0 1 .4 1 1V20c0 .6-.4 1-1 1A17 17 0 0 1 3 4c0-.6.4-1 1-1h3.5c.6 0 1 .4 1 1 0 1.3.2 2.5.6 3.6.1.3 0 .7-.2 1z"/></svg>
    215.555.0142
  </a>
</header>

<section class="hero">
  <div class="photo" role="img" aria-label="Photo of a doctor in a white coat consulting with a patient at a desk" style="left:0;top:125px;width:1200px;height:570px;background:linear-gradient(90deg,#f2f3f4 0%,#eceef0 45%,#c9ccd0 70%,#6d7178 100%)"></div>
  <svg class="abs" style="left:0;top:590px" width="1200" height="110"><polygon points="0,8 1200,105 1200,110 0,110" fill="#fff"/></svg>
  <h1 class="abs hero-title"><span class="accent">Verantel</span> Dx</h1>
  <p class="abs hero-sub">Medical Diagnostics<br>Consulting</p>
  <a class="btn" style="left:78px;top:450px;width:144px;height:47px">CONTACT US</a>
</section>

<section class="about">
  <div class="photo" role="img" aria-label="Photo of a team of colleagues reviewing work at a laptop" style="left:78px;top:739px;width:499px;height:332px;background:linear-gradient(135deg,#dfe4ea,#b9c3ce 60%,#8f9aa6)"></div>
  <h2 class="abs section-title" style="left:642px;top:730px">About <span class="accent">Verantel Dx</span></h2>
  <p class="abs para" style="left:642px;top:808px;width:480px">Lorem ipsum dolor sit amet, consectetur adipiscing elit, sed do eiusmod tempor incididunt ut labore et dolore magna aliqua. Ut enim ad minim veniam, quis nostrud exercitation ullamco laboris nisi ut aliquip ex ea commodo consequat. Duis aute irure dolor in reprehenderit in voluptate velit esse cillum dolore eu fugiat nulla pariatur. Excepteur sint occaecat cupidatat non proident, sunt in culpa qui officia deserunt mollit anim id est laborum.</p>
  <a class="btn" style="left:640px;top:1020px;width:144px;height:50px">READ MORE</a>
</section>

<section class="services">
  <div class="photo" role="img" aria-label="Dark background photo of laboratory staff at work" style="left:0;top:1110px;width:1200px;height:760px;background:linear-gradient(120deg,#4a5666,#2e3a4a 50%,#3b4757)"></div>
  <svg class="abs" style="left:0;top:1105px" width="1200" height="770">
    <polygon points="0,0 1200,0 1200,8 0,110" fill="#fff"/>
    <polygon points="0,50 360,80 0,112" fill="var(--blue)"/>
    <polygon points="760,745 1200,708 1200,770 1180,770" fill="var(--blue)"/>
    <polygon points="0,755 760,745 1180,770 0,770" fill="#fff"/>
  </svg>
  <h2 class="abs section-title" style="left:0;width:1200px;text-align:center;top:1240px;color:#fff;font-size:42px">Verantel Dx <span class="accent">Services</span></h2>

  <div class="card" style="left:78px">
    <div class="photo" role="img" aria-label="Photo of doctors reviewing a chart" style="background:linear-gradient(135deg,#e6eaee,#b8c2cc)"></div>
    <h3>Developement</h3>
    <p>Lorem ipsum dol amet, consectetur adipiscing elit, sed do eiusmod tempor incididunt ut labore et dolore magna aliqua.</p>
    <span class="more">READ MORE</span>
  </div>
  <div class="card" style="left:433px">
    <div class="photo" role="img" aria-label="Photo of a meeting around a conference table" style="background:linear-gradient(135deg,#e9edf1,#a9b6c3)"></div>
    <h3>Marketing</h3>
    <p>Lorem ipsum dol amet, consectetur adipiscing elit, sed do eiusmod tempor incididunt ut labore et dolore magna aliqua.</p>
    <span class="more">READ MORE</span>
  </div>
  <div class="card" style="left:789px">
    <div class="photo" role="img" aria-label="Photo of colleagues working at a laptop" style="background:linear-gradient(135deg,#e3e8ed,#b4bfca)"></div>
    <h3>Monitoring</h3>
    <p>Lorem ipsum dol amet, consectetur adipiscing elit, sed do eiusmod tempor incididunt ut labore et dolore magna aliqua.</p>
    <span class="more">READ MORE</span>
  </div>
</section>

<section class="feedback">
  <h2 class="abs section-title" style="left:0;width:1200px;text-align:center;top:1905px;font-size:42px">Clients <span class="accent">Feedback</span></h2>
  <div class="arrow" style="left:78px;border:1px solid var(--blue)"><svg width="12" height="20" viewBox="0 0 12 20" fill="none" stroke="var(--blue)" stroke-width="1.6"><polyline points="10,2 2,10 10,18"/></svg></div>
  <div class="arrow" style="left:1087px;background:var(--blue)"><svg width="12" height="20" viewBox="0 0 12 20" fill="none" stroke="#fff" stroke-width="1.6"><polyline points="2,2 10,10 2,18"/></svg></div>

  <div class="quote" style="left:162px">
    <svg width="32" height="26" viewBox="0 0 32 26" fill="var(--blue)"><path d="M0 26V14C0 6 4 1 12 0v5c-4 1-6 4-6 8h6v13zM18 26V14c0-8 4-13 12-14v5c-4 1-6 4-6 8h6v13z"/></svg>
    <p>Lorem ipsum dolor sit amet, consectetur adipiscing elit, sed do eiusmod tempor incididunt ut labore et dolore magna aliqua.</p>
    <span class="who">- Client Name</span>
  </div>
  <div class="quote" style="left:464px">
    <svg width="32" height="26" viewBox="0 0 32 26" fill="var(--blue)"><path d="M0 26V14C0 6 4 1 12 0v5c-4 1-6 4-6 8h6v13zM18 26V14c0-8 4-13 12-14v5c-4 1-6 4-6 8h6v13z"/></svg>
    <p>Lorem ipsum dolor sit amet, consectetur adipiscing elit, sed do eiusmod tempor incididunt ut labore et dolore magna aliqua.</p>
    <span class="who">- Client Name</span>
  </div>
  <div class="quote" style="left:766px">
    <svg width="32" height="26" viewBox="0 0 32 26" fill="var(--blue)"><path d="M0 26V14C0 6 4 1 12 0v5c-4 1-6 4-6 8h6v13zM18 26V14c0-8 4-13 12-14v5c-4 1-6 4-6 8h6v13z"/></svg>
    <p>Lorem ipsum dolor sit amet, consectetur adipiscing elit, sed do eiusmod tempor incididunt ut labore et dolore magna aliqua.</p>
    <span class="who">- Client Name</span>
  </div>
</section>

<section class="contact">
  <div class="photo" role="img" aria-label="Blue-tinted photo of a clinician's hands at a desk" style="left:0;top:2320px;width:1200px;height:600px;background:linear-gradient(160deg,#3d8ff0,#2a82ea 50%,#4c98f0)"></div>
  <svg class="abs" style="left:0;top:2315px" width="1200" height="610">
    <polygon points="0,0 1200,0 1200,70 0,8" fill="#fff"/>
    <polygon points="840,72 1200,40 1200,110" fill="var(--black)"/>
    <polygon points="0,525 420,560 0,600" fill="var(--black)"/>
    <polygon points="0,600 420,560 1200,610 0,610" fill="#fff"/>
  </svg>
  <h2 class="abs section-title" style="left:0;width:1200px;text-align:center;top:2448px;color:#fff;font-size:42px">Contact Us</h2>
  <div class="field" style="left:256px;top:2540px;width:218px;height:62px">Name :</div>
  <div class="field" style="left:490px;top:2540px;width:218px;height:62px">Email :</div>
  <div class="field" style="left:724px;top:2540px;width:219px;height:62px">Phone :</div>
  <div class="field" style="left:256px;top:2620px;width:687px;height:102px;padding-top:12px">Message / Comments :</div>
  <a class="btn" style="left:527px;top:2738px;width:146px;height:52px;background:#22262b;box-shadow:none">READ MORE</a>
</section>

<section class="news">
  <h2 class="abs section-title" style="left:0;width:1200px;text-align:center;top:2937px;font-size:42px">Recent <span class="accent">News Updates</span></h2>

  <div class="photo" role="img" aria-label="Photo of two young doctors smiling at a desk" style="left:78px;top:3030px;width:499px;height:270px;background:linear-gradient(135deg,#d9e6f2,#a7bdd3)"></div>
  <div class="photo" role="img" aria-label="Photo of a doctor showing a tablet to a mother and child" style="left:623px;top:3030px;width:499px;height:270px;background:linear-gradient(135deg,#e8e2dc,#b9b0a8)"></div>

  <div class="meta" style="left:78px">
    <span><svg width="14" height="14" viewBox="0 0 14 14" fill="var(--blue)"><rect x="1" y="3" width="12" height="10" rx="1"/><rect x="3" y="1" width="2" height="3"/><rect x="9" y="1" width="2" height="3"/></svg>June 17, 2019</span>
    <span><svg width="18" height="14" viewBox="0 0 18 14" fill="none" stroke="var(--blue)" stroke-width="1.5"><path d="M2 2h14v8H7l-4 3V10H2z"/></svg>0 Comments</span>
    <span><svg width="14" height="14" viewBox="0 0 14 14" fill="var(--blue)"><circle cx="7" cy="4" r="3"/><path d="M1 14c0-4 3-6 6-6s6 2 6 6z"/></svg>Lena K.</span>
  </div>
  <div class="meta" style="left:623px">
    <span><svg width="14" height="14" viewBox="0 0 14 14" fill="var(--blue)"><rect x="1" y="3" width="12" height="10" rx="1"/><rect x="3" y="1" width="2" height="3"/><rect x="9" y="1" width="2" height="3"/></svg>June 17, 2019</span>
    <span><svg width="18" height="14" viewBox="0 0 18 14" fill="none" stroke="var(--blue)" stroke-width="1.5"><path d="M2 2h14v8H7l-4 3V10H2z"/></svg>0 Comments</span>
    <span><svg width="14" height="14" viewBox="0 0 14 14" fill="var(--blue)"><circle cx="7" cy="4" r="3"/><path d="M1 14c0-4 3-6 6-6s6 2 6 6z"/></svg>Lena K.</span>
  </div>

  <h3 class="news-title" style="left:79px">Lorem ipsum dolor sit amet, consectetur adipiscing dolore magna aliqua.</h3>
  <h3 class="news-title" style="left:625px">Lorem ipsum dolor sit amet, consectetur adipiscing dolore magna aliqua.</h3>
  <p class="news-para" style="left:79px">Lorem ipsum dolor sit amet, consectetur adipiscing elit, sed do eiusmod tempor incididunt ut labore et dolore magna aliqua. Ut enim ad minim veniam, ut aliquip ex ea commodo consequat.</p>
  <p class="news-para" style="left:625px">Lorem ipsum dolor sit amet, consectetur adipiscing elit, sed do eiusmod tempor incididunt ut labore et dolore magna aliqua. Ut enim ad minim veniam, ut aliquip ex ea commodo consequat.</p>
  <a class="btn" style="left:78px;top:3520px;width:144px;height:49px">READ MORE</a>
  <a class="btn" style="left:623px;top:3520px;width:144px;height:49px">READ MORE</a>
</section>

<footer>
  <svg class="abs" style="left:0;top:3630px" width="1200" height="537">
    <polygon points="0,0 1200,75 1200,537 0,537" fill="var(--blue)"/>
    <polygon points="0,0 1200,75 1200,0" fill="#fff"/>
    <polygon points="840,110 1200,65 1200,110" fill="var(--black)"/>
    <polygon points="840,110 1200,110 1200,128" fill="var(--black)"/>
  </svg>

  <h4 class="foot-h" style="left:78px">Quick Links</h4>
  <ul class="foot-list" style="left:78px"><li>Home</li><li>About</li><li>Services</li><li>News</li><li>Contact</li></ul>

  <h4 class="foot-h" style="left:348px">Services</h4>
  <ul class="foot-list" style="left:348px"><li>Developement</li><li>Marketing</li><li>Monitoring</li></ul>

  <h4 class="foot-h" style="left:616px">Come Find Us</h4>
  <div class="contact-row" style="top:3826px"><svg width="20" height="20" viewBox="0 0 24 24" fill="#fff"><path d="M6.6 10.8a15.1 15.1 0 0 0 6.6 6.6l2.2-2.2c.3-.3.7-.4 1-.2 1.1.4 2.3.6 3.6.6.6 0 1 .4 1 1V20c0 .6-.4 1-1 1A17 17 0 0 1 3 4c0-.6.4-1 1-1h3.5c.6 0 1 .4 1 1 0 1.3.2 2.5.6 3.6.1.3 0 .7-.2 1z"/></svg>215.555.0142</div>
  <div class="contact-row" style="top:3870px"><svg width="20" height="16" viewBox="0 0 20 16" fill="#fff"><rect x="0" y="1" width="20" height="14" rx="1"/><polyline points="1,2 10,9 19,2" fill="none" stroke="var(--blue)" stroke-width="1.6"/></svg>info@verantel-dx.com</div>
  <div class="contact-row" style="top:3916px"><svg width="20" height="22" viewBox="0 0 20 24" fill="#fff"><path d="M10 0a8 8 0 0 0-8 8c0 6 8 16 8 16s8-10 8-16a8 8 0 0 0-8-8zm0 11a3 3 0 1 1 0-6 3 3 0 0 1 0 6z"/></svg><span>123, Address, State Name,<br>City Name,Zipcode</span></div>

  <h4 class="foot-h" style="left:885px">Stay Connected</h4>
  <span class="social" style="left:883px" role="img" aria-label="Social link"></span>
  <span class="social" style="left:935px" role="img" aria-label="Social link"></span>
  <span class="social" style="left:987px" role="img" aria-label="Social link"></span>
  <span class="social" style="left:1039px" role="img" aria-label="Social link"></span>

  <div class="abs" style="left:78px;top:4034px;width:460px;height:1px;background:rgba(255,255,255,.45)"></div>
  <div class="abs" style="left:662px;top:4034px;width:460px;height:1px;background:rgba(255,255,255,.45)"></div>
  <div class="abs foot-brand"><i></i>Verantel Dx</div>

  <p class="copyright">Copyright © <b>Verantel Dx</b> - 2019 . All Right Reserved</p>
</footer>

</body>
</html>
```